tallow-brook.com

We are a small dollar lending company that will revolutionize the industry. We will do this by being completely transparent, fee free, etc and an interest rate that normal people can afford to pay. Over 10X less than our competition. We only allow our members to pay bills " bills paid fast", within 72 hours. Payday loans typically charge from 390%-600% with a terrible payback structure. We charge 36%, period, with a payback structure over 12 months. Our site will be very simple and easy to use but elegant at the same time. We do not want the site to be too busy, less is more and easier. We will have; Home, The Story, Why tallowbrook.com, Are you eligible? Members, Clients. To become a member you have to be referred by a current client of tallowbrook.com. A lot of the busy stuff will be saved for the Members and Clients sections. The feel must be elegant, easy to use and very simple to understand. I am looking for the green, white and black combinations of colors, very similar to my logo that was designed by Fernquillo.

```html
<!DOCTYPE html>
<html lang="en">
<head>
<meta charset="utf-8">
<title>Tallow Brook — Bills Paid Fast</title>
<link rel="stylesheet" href="https://fonts.googleapis.com/css2?family=Open+Sans:ital,wght@0,300;0,400;0,600;1,400&display=swap">
<style>
:root{
  --green:#8cc63f;
  --green-dark:#79b02f;
  --black:#000;
  --ink:#333;
  --muted:#777;
  --line:#e3e3e3;
  --footer:#363636;
  --white:#fff;
}
*{margin:0;padding:0;box-sizing:border-box}
html,body{width:970px;height:1200px;overflow:hidden;background:var(--white)}
body{position:relative;font-family:"Open Sans",Arial,sans-serif;color:var(--ink)}
.abs{position:absolute}

/* header */
.site-header{left:0;top:0;width:970px;height:59px;background:var(--green)}
.brand{left:106px;top:15px;display:flex;align-items:center;gap:7px;color:var(--white);font-size:16px;font-weight:400;letter-spacing:.2px;white-space:nowrap}
.brand-dot{width:24px;height:24px;border:3px solid var(--white);border-radius:50%}
.main-nav{right:106px;top:0;height:59px;display:flex}
.main-nav a{display:block;height:59px;line-height:59px;padding:0 11px;color:var(--white);text-decoration:none;font-size:12px;white-space:nowrap}
.main-nav a.active{background:var(--green-dark)}

/* hero */
.hero{left:0;top:59px;width:970px;height:389px;background:radial-gradient(ellipse at 55% 35%,#b9b3a6 0%,#7b7467 35%,#3b3a3a 70%,#1d1e22 100%)}
.hero-title{left:294px;top:204px;width:382px;height:75px;background:var(--black);color:var(--white);font-weight:300;font-size:56px;line-height:75px;text-align:center}
.hero-login{left:420px;top:298px;width:129px;height:47px;background:var(--green);color:var(--white);font-size:17px;font-weight:600;line-height:47px;text-align:center}
.hero-arrow{top:237px;width:32px;height:32px}

/* features */
.feature{top:478px;width:180px;text-align:center}
.feature-icon{height:52px;display:flex;justify-content:center;align-items:center}
.feature h3{margin-top:13px;font-weight:400;font-size:16px;color:var(--ink)}
.feature p{margin-top:8px;font-size:10px;line-height:15px;color:var(--muted)}
.btn-more{display:inline-block;margin-top:10px;width:85px;height:26px;line-height:26px;background:var(--green);color:var(--white);font-size:11px;font-style:italic}

.rule{left:102px;width:762px;height:1px;background:var(--line)}

/* info columns */
.heading{font-weight:400;font-size:16px;color:var(--black);white-space:nowrap}
.copy{font-size:9.5px;line-height:16.6px;color:var(--muted)}
.link{font-size:11.5px;font-style:italic;color:var(--green)}
.ticks{list-style:none}
.ticks li{position:relative;padding-left:17px;font-size:9.5px;line-height:22px;color:var(--ink);white-space:nowrap}
.ticks li::before{content:"";position:absolute;left:0;top:6px;width:9px;height:9px;border-radius:50%;background:var(--green)}

.enquiry{left:636px;top:702px;width:226px;height:240px;border:1px solid var(--line);border-radius:3px;box-shadow:0 0 3px rgba(0,0,0,.08);padding:0 16px}
.enquiry h2{margin-top:10px;text-align:center;color:var(--green);font-weight:400;font-size:20px;letter-spacing:.5px}
.field{margin-top:9px;height:22px;border:1px solid #ccc;border-radius:2px;background:linear-gradient(#fff,#f4f4f4);font-size:9px;line-height:20px;padding-left:7px;color:#888}
.field:first-of-type{margin-top:10px}
.submit{display:block;margin:13px auto 0;width:92px;height:25px;background:var(--black);color:var(--white);font-size:11px;font-weight:600;line-height:25px;text-align:center}

/* clients */
.clients-title{left:105px;top:995px;font-size:16px;font-weight:400;color:var(--black)}
.pager{top:1000px;width:19px;height:18px;background:var(--green)}
.client-row{left:106px;top:1034px;width:758px;height:66px;border:1px solid #ececec;display:flex}
.client{flex:1;border-right:1px solid #ececec;display:flex;align-items:center;justify-content:center;gap:6px;font-size:13px;font-weight:600;color:var(--ink);white-space:nowrap}
.client:last-child{border-right:0}
.client i{width:10px;height:10px;background:var(--green);display:block}

/* footer */
.site-footer{left:0;top:1128px;width:970px;height:72px;background:var(--footer)}
.foot-nav{left:106px;top:1150px;font-size:11px;color:var(--white);white-space:nowrap}
.copyright{left:107px;top:1177px;font-size:9.5px;color:#ddd}
.social{left:680px;top:1155px;display:flex;gap:8px}
.social span{width:24px;height:24px;border-radius:3px;background:var(--green);display:block}
</style>
</head>
<body>

<header class="site-header abs"></header>
<div class="brand abs"><span class="brand-dot"></span>TALLOW BROOK</div>
<nav class="main-nav abs">
  <a class="active">HOME</a><a>THE STORY</a><a>WHY TALLOWBROOK.COM</a><a>ARE YOU ELIGIBLE? MEMBERS</a><a>CLIENTS</a>
</nav>

<section class="hero abs" role="img" aria-label="Photo of a hand in a suit sleeve holding out a dollar bill"></section>
<svg class="hero-arrow abs" style="left:19px" viewBox="0 0 32 32"><circle cx="16" cy="16" r="14.5" fill="none" stroke="#fff" stroke-width="2"/><path d="M20 8 L10 16 L20 24 L17 16 Z" fill="#fff"/></svg>
<svg class="hero-arrow abs" style="left:920px" viewBox="0 0 32 32"><circle cx="16" cy="16" r="14.5" fill="none" stroke="#fff" stroke-width="2"/><path d="M12 8 L22 16 L12 24 L15 16 Z" fill="#fff"/></svg>
<div class="hero-title abs">Bills Paid Fast</div>
<div class="hero-login abs">LOGIN HERE</div>

<div class="feature abs" style="left:102px">
  <div class="feature-icon"><svg width="52" height="50" viewBox="0 0 52 50"><circle cx="19" cy="31" r="12" fill="none" stroke="#8cc63f" stroke-width="8" stroke-dasharray="5 3.4"/><circle cx="19" cy="31" r="8" fill="#8cc63f"/><circle cx="19" cy="31" r="3.5" fill="#fff"/><circle cx="39" cy="13" r="8" fill="none" stroke="#8cc63f" stroke-width="6" stroke-dasharray="3.5 2.8"/><circle cx="39" cy="13" r="5" fill="#8cc63f"/><circle cx="39" cy="13" r="2" fill="#fff"/></svg></div>
  <h3>PAYMENT SERVICES</h3>
  <p>Praesent vestibulum molestie lacus. Aenean noy henghgkdrerit mauris. Phasel Fusce suscipit varius mi.</p>
  <span class="btn-more">READ MORE</span>
</div>
<div class="feature abs" style="left:296px">
  <div class="feature-icon"><svg width="48" height="48" viewBox="0 0 48 48"><path d="M28 2 H46 V20 L22 44 L4 26 Z" fill="#8cc63f"/><circle cx="38" cy="10" r="3" fill="#fff"/></svg></div>
  <h3>PAYMENT SERVICES</h3>
  <p>Praesent vestibulum molestie lacus. Aenean noy henghgkdrerit mauris. Phasel Fusce suscipit varius mi.</p>
  <span class="btn-more">READ MORE</span>
</div>
<div class="feature abs" style="left:486px">
  <div class="feature-icon"><span style="font-size:54px;font-weight:600;color:var(--green);line-height:52px">$</span></div>
  <h3>PAYMENT SERVICES</h3>
  <p>Praesent vestibulum molestie lacus. Aenean noy henghgkdrerit mauris. Phasel Fusce suscipit varius mi.</p>
  <span class="btn-more">READ MORE</span>
</div>
<div class="feature abs" style="left:681px">
  <div class="feature-icon"><svg width="52" height="40" viewBox="0 0 52 40"><rect x="22" y="4" width="28" height="7" rx="3.5" fill="#8cc63f"/><rect x="22" y="15" width="28" height="7" rx="3.5" fill="#8cc63f"/><rect x="22" y="26" width="28" height="7" rx="3.5" fill="#8cc63f"/><circle cx="16" cy="24" r="13" fill="#fff" stroke="#8cc63f" stroke-width="3"/><text x="16" y="30" font-size="16" font-weight="700" text-anchor="middle" fill="#8cc63f" font-family="Open Sans,sans-serif">$</text></svg></div>
  <h3>PAYMENT SERVICES</h3>
  <p>Praesent vestibulum molestie lacus. Aenean noy henghgkdrerit mauris. Phasel Fusce suscipit varius mi.</p>
  <span class="btn-more">READ MORE</span>
</div>

<div class="rule abs" style="top:672px"></div>

<!-- about column -->
<h2 class="heading abs" style="left:107px;top:699px">ABOUT TALLOW BROOK</h2>
<p class="copy abs" style="left:107px;top:724px;width:250px">We are heavily customer service oriented and under stand the needs of small and medium businesses, enab and the needs of small to medium businesses, enab ling th to medium businesses and the needs of small to medium businesses.</p>
<ul class="ticks abs" style="left:107px;top:815px">
  <li>Neque porro quis quamns ectetunsectetu est quo</li>
  <li>Rem ipsum quia dolor snsectetuit nsectetu ame</li>
  <li>Consectetur, adipisci vnsectetu elitnsectetu</li>
  <li>Neque porro quisquam est qui dolo</li>
  <li>Rem ipsum quia dolor sitnsectet unsectetu ame</li>
</ul>
<span class="link abs" style="left:107px;top:930px">Read More</span>

<!-- eligibility column -->
<h2 class="heading abs" style="left:380px;top:699px">ARE YOU ELIGIBLE</h2>
<p class="copy abs" style="left:380px;top:722px;width:235px">We are heavily customer service oriented and unders tand the needs of small to medium businesses, enab and the needs of small to medium businesses, enab ling th to medium businesses.</p>
<span class="link abs" style="left:380px;top:796px">Read More</span>
<h2 class="heading abs" style="left:380px;top:832px">MEMBERSHIP NOW!</h2>
<p class="copy abs" style="left:380px;top:855px;width:235px">We are heavily customer service oriented and unders tand the needs of small to medium businesses, enab and the needs of small to medium businesses, enab ling th to medium businesses.</p>
<span class="link abs" style="left:380px;top:930px">Read More</span>

<form class="enquiry abs">
  <h2>ENQUIRY FORM</h2>
  <div class="field">Enter Name:</div>
  <div class="field">Enter Email Address:</div>
  <div class="field">Phone Number:</div>
  <div class="field">Price Range:</div>
  <div class="field">Subject:</div>
  <span class="submit">SUBMIT NOW</span>
</form>

<div class="rule abs" style="top:974px"></div>

<h2 class="clients-title abs">OUR CLIENTS</h2>
<svg class="pager abs" style="left:820px" viewBox="0 0 19 18"><rect width="19" height="18" fill="#8cc63f"/><path d="M11 5 L7 9 L11 13" fill="none" stroke="#fff" stroke-width="1.5"/></svg>
<svg class="pager abs" style="left:845px" viewBox="0 0 19 18"><rect width="19" height="18" fill="#8cc63f"/><path d="M8 5 L12 9 L8 13" fill="none" stroke="#fff" stroke-width="1.5"/></svg>
<div class="client-row abs">
  <div class="client"><i></i>Harwell Cable</div>
  <div class="client"><i></i>Ostrin Finance</div>
  <div class="client"><i></i>Mossgate Capital</div>
  <div class="client"><i></i>Kestrel Union Bank</div>
  <div class="client"><i></i>Brightmere</div>
</div>

<footer class="site-footer abs"></footer>
<div class="foot-nav abs">HOME &nbsp;|&nbsp; THE STORY &nbsp;|&nbsp; WHY TALLOWBROOK.COM &nbsp;|&nbsp; ARE YOU ELIGIBLE? MEMBERS &nbsp;|&nbsp; CLIENTS</div>
<div class="copyright abs">Copyright © 2014 are reserved</div>
<div class="social abs"><span></span><span></span><span></span><span></span><span></span><span></span></div>

</body>
</html>
```